Bright Towns Forum PowerPoint Design Template and Sample Deck

The Bright Towns Forum is an international organization that seeks to improve the livability, workability and sustainability of the world’s cities.
We seek a versatile PowerPoint design template with 10 slide types plus a “self-documenting” sample deck. Your design will be used in keynote speeches and workshops around the world.
After the contest is completed, we will ask the winning designer to add 10-20 additional slide types for $75 per slide. We also seek a long-term relationship whereby we can request “custom” slides and/or ask the designer to touch up the slides we build to make them better.
FILES. We have uploaded several files:
2. PALETTE. Shows our official colors.
3 LOGOS. Several individual files with different variations of our logo. Some with our motto, some without.
2. SAMPLE SLIDES. Because we were unable to successfully upload our sample deck, we are making it available via this FileNook link:
https://www.filenook-example.com/s/k7qrtmzp2wd9hxa/The%20Bright%20Towns%20Forum%20Design%20Contest%20Notes.docx?dl=0
Target Market(s)
Mayors, department heads, CIOs, senior executives from technology companies
Industry/Entity Type
Information Technology
Colors
Designer to choose colors to be used in the design.
Requirements
Must have
- Please see uploaded Word document for requirements, nice to haves and should not haves and uploaded palette for color preferences.
Nice to have
- see above
Should not have
- see above

```html
<!DOCTYPE html>
<html lang="en">
<head>
<meta charset="utf-8">
<title>Bright Towns Forum – Deck Overview</title>
<link href="https://fonts.googleapis.com/css2?family=Open+Sans:wght@300;400;600;700;800&display=swap" rel="stylesheet">
<style>
:root{
  --navy:#17335f;
  --navy-deep:#0f2547;
  --blue:#3b6cb3;
  --blue-soft:#7ea3d6;
  --orange:#f28a1c;
  --green:#8bbf3a;
  --purple:#7d5ba6;
  --red-orange:#ee5b2a;
  --ink:#2b2b2b;
  --grey:#7a7a7a;
  --line:#d5d9df;
  --page:#e4e5e7;
}
*{box-sizing:border-box;margin:0;padding:0}
html,body{width:1200px;height:914px;overflow:hidden;background:var(--page);font-family:"Open Sans",Arial,sans-serif;color:var(--ink)}
.deck{position:relative;width:1200px;height:914px}
.slide{position:absolute;width:391px;height:220px;background:#fff;overflow:hidden;box-shadow:0 1px 3px rgba(0,0,0,.18)}
.abs{position:absolute}
.stripe{position:absolute;left:0;top:0;bottom:0;width:16px;background:linear-gradient(90deg,var(--navy-deep) 0 9px,var(--blue) 9px 14px,transparent 14px)}
.title{position:absolute;left:28px;top:10px;font-size:14.5px;font-weight:700;color:#1b1b1b;letter-spacing:.2px}
.title b{color:var(--orange);font-weight:700}
.brand{position:absolute;right:30px;top:11px;font-size:6.5px;font-weight:600;color:var(--navy)}
.pageno{position:absolute;right:0;top:7px;width:27px;height:14px;background:var(--navy);color:#fff;font-size:5px;font-weight:700;display:flex;align-items:center;justify-content:center}
.photo{position:absolute}
.orange{color:var(--orange)}
.small{font-size:6px;color:var(--grey);line-height:1.45}
.pill{position:absolute;border-radius:10px;display:flex;align-items:center;justify-content:center;font-size:6.5px}
.region-name{font-size:11px;color:var(--orange)}
.region-name b{font-weight:600;color:var(--navy)}
.note{font-size:6.8px;color:#666;line-height:1.4}
.note b{color:#444}
</style>
</head>
<body>
<div class="deck">

<!-- 1 Title -->
<section class="slide" style="left:6px;top:6px">
  <div class="photo" role="img" aria-label="City skyline across a river with a suspension bridge" style="left:0;top:0;width:391px;height:145px;background:linear-gradient(180deg,#8e97a3 0%,#a9b0ba 45%,#5b6572 70%,#39424d 100%)"></div>
  <div class="abs" style="right:30px;top:8px;text-align:right;font-size:4.6px;color:#fff;line-height:2.6">+1 234 5678<br>hello@brightforum.org<br>2nd floor Harbor House,<br>Lakeport, US</div>
  <svg class="abs" style="right:10px;top:8px" width="10" height="42" viewBox="0 0 10 42"><path d="M2 1c1 3 3 6 7 7l1-2-2-1-1 1c-1-1-2-2-3-3l1-1-1-2z" fill="#f28a1c"/><rect x="1" y="17" width="8" height="6" fill="#f28a1c"/><path d="M5 32a3 3 0 1 1 0 .1zM5 38l-3-4h6z" fill="none" stroke="#f28a1c" stroke-width="1.3"/></svg>
  <div class="abs" style="left:0;top:145px;width:391px;height:60px;background:#fff"></div>
  <div class="abs" style="left:114px;top:155px;font-size:16.5px;font-weight:300;color:var(--navy);letter-spacing:.2px">THE WORLD IS <b style="font-weight:600">CHANGING</b></div>
  <div class="abs" style="left:117px;top:178px;font-size:7.6px;color:var(--orange)">“The biggest shift in economic gravity in history.”</div>
  <div class="abs" style="left:267px;top:190px;font-size:4.6px;color:var(--grey);font-style:italic">- Halvorsen &amp; Co.</div>
  <div class="abs" style="left:318px;top:151px;width:1px;height:46px;background:var(--line)"></div>
  <div class="abs" style="left:328px;top:150px;font-size:12.5px;line-height:1;color:var(--navy)">Bright<br>Towns<br>Forum</div>
  <div class="abs" style="left:0;top:205px;width:391px;height:15px;background:#2a2d33"></div>
</section>

<!-- 2 Content Agenda -->
<section class="slide" style="left:404px;top:6px">
  <div class="photo" role="img" aria-label="Business people in a bright office, tinted blue" style="left:0;top:0;width:184px;height:220px;background:linear-gradient(160deg,#5d80b6,#3e62a0 60%,#2d4f8a)"></div>
  <div class="stripe"></div>
  <div class="abs" style="left:22px;top:10px;font-size:14px;font-weight:700;color:#fff">CONTENT <span class="orange">AGENDA</span></div>
  <div class="abs" style="left:90px;top:55px;font-size:8.5px;font-weight:600;color:#fff">2017 AGENDA</div>
  <div class="abs" style="left:90px;top:119px;font-size:8.5px;font-weight:600;color:#fff">2018 AGENDA</div>
  <div class="abs" style="left:163px;top:68px;width:22px;height:48px;background:var(--navy);color:#fff;font-size:6.5px;text-align:center;line-height:16px">02<br>03<br>04</div>
  <div class="abs" style="left:163px;top:133px;width:22px;height:48px;background:var(--navy);color:#fff;font-size:6.5px;text-align:center;line-height:16px">06<br>07<br>08</div>
  <div class="brand">Bright Towns Forum</div><div class="pageno">2</div>
  <div class="abs" style="left:194px;top:55px;width:180px;font-size:7.5px;line-height:16px;color:#555">
    <div style="display:flex;justify-content:space-between;color:var(--orange);font-weight:600;border-bottom:1px solid var(--line)"><span>RECAP &amp; REPORT</span><span>01</span></div>
    <div style="display:flex;justify-content:space-between;border-bottom:1px solid var(--line)"><span>UPGRADE</span><span>02</span></div>
    <div style="display:flex;justify-content:space-between;border-bottom:1px solid var(--line)"><span>RULES</span><span>03</span></div>
    <div style="display:flex;justify-content:space-between;border-bottom:1px solid var(--line)"><span>SPONSORSHIP</span><span>04</span></div>
    <div style="display:flex;justify-content:space-between;color:var(--orange);font-weight:600;border-bottom:1px solid var(--line)"><span>RECAP &amp; REPORT</span><span>05</span></div>
    <div style="display:flex;justify-content:space-between;border-bottom:1px solid var(--line)"><span>UPGRADE</span><span>06</span></div>
    <div style="display:flex;justify-content:space-between;border-bottom:1px solid var(--line)"><span>RULES</span><span>07</span></div>
    <div style="display:flex;justify-content:space-between"><span>SPONSORSHIP</span><span>08</span></div>
  </div>
</section>

<!-- 3 Cities are transforming -->
<section class="slide" style="left:802px;top:6px">
  <div class="photo" role="img" aria-label="Aerial view of dense downtown towers" style="left:0;top:0;width:391px;height:220px;background:linear-gradient(135deg,#9aa3ad,#5f6b78 50%,#3c4653)"></div>
  <div class="abs" style="left:0;top:0;width:188px;height:220px;background:rgba(23,51,95,.93)"></div>
  <div class="brand">Bright Towns Forum</div><div class="pageno">3</div>
  <div class="abs" style="left:0;top:36px;width:188px;text-align:center;font-size:13.5px;font-weight:700;color:#fff;line-height:1.25">CITIES ARE<br><span class="orange">TRANSFORMING</span></div>
  <div class="abs" style="left:86px;top:77px;width:16px;height:2px;background:var(--orange)"></div>
  <div class="abs" style="left:44px;top:92px;width:120px;text-align:center;font-size:7.6px;color:#dfe6f2;line-height:1.5"><b style="color:#fff;font-weight:600">For those of us living in cities,</b> we need to make sure they are smart cities. Nothing else makes sense</div>
  <div class="pill" style="left:58px;top:162px;width:102px;height:14px;background:var(--blue-soft);color:#fff;justify-content:flex-start"><span style="width:22px;height:14px;border-radius:7px;background:var(--green);display:flex;align-items:center;justify-content:center"><svg width="7" height="7" viewBox="0 0 10 10"><circle cx="5" cy="5" r="4" fill="none" stroke="#fff"/><path d="M1 5h8M5 1v8" stroke="#fff" stroke-width=".8"/></svg></span><span style="margin-left:20px">Visit Us</span></div>
</section>

<!-- 4 Quote -->
<section class="slide" style="left:6px;top:233px">
  <div class="abs" style="left:0;top:0;width:391px;height:220px;background:linear-gradient(90deg,#1d3f73,#2a5590 55%,#5d7fae)"></div>
  <div class="photo" role="img" aria-label="Portrait of a thoughtful senior woman resting her chin on her hand" style="left:215px;top:0;width:176px;height:220px;background:linear-gradient(90deg,rgba(42,85,144,0),#8b8f9a 45%,#b9a7a1)"></div>
  <div class="stripe"></div>
  <div class="brand" style="color:#fff">Bright Towns Forum</div><div class="pageno">4</div>
  <svg class="abs" style="left:76px;top:17px" width="32" height="28" viewBox="0 0 32 28"><ellipse cx="13" cy="12" rx="11" ry="9" fill="none" stroke="#fff" stroke-width="1.4"/><ellipse cx="20" cy="15" rx="10" ry="8" fill="none" stroke="#fff" stroke-width="1.4"/><path d="M6 20l-3 6 7-4" fill="none" stroke="#fff" stroke-width="1.4"/></svg>
  <div class="abs" style="left:31px;top:62px;width:180px;color:#fff;font-size:7.7px;line-height:1.4">For those of us living in cities, we need to make sure they are smart cities.</div>
  <div class="abs" style="left:31px;top:85px;font-size:14px;line-height:1.05;color:var(--orange)">Nothing else makes<br>sense</div>
  <div class="abs" style="left:31px;top:120px;font-size:8px;color:#fff">And nothing else is such a world-wide</div>
  <div class="abs" style="left:31px;top:133px;font-size:11.5px;font-weight:600;color:var(--green)">Economic Opportunity</div>
  <div class="pill" style="left:31px;top:166px;width:152px;height:27px;border-radius:14px;background:var(--blue-soft);color:#fff;flex-direction:column;font-size:6px;line-height:1.4"><b style="font-weight:600">Marta Veldhuis,</b>Vice Chair - Continental Board</div>
</section>

<!-- 5 2018 Program -->
<section class="slide" style="left:404px;top:233px">
  <div class="photo" role="img" aria-label="Faded image of a laptop on a desk" style="left:190px;top:0;width:201px;height:220px;background:linear-gradient(90deg,#fff,#eef1f5 40%,#dfe4ea)"></div>
  <div class="stripe"></div>
  <div class="title">2018 <b>PROGRAM</b></div>
  <div class="abs" style="left:28px;top:30px;width:14px;height:2px;background:var(--orange)"></div>
  <div class="brand">Bright Towns Forum</div><div class="pageno">5</div>
  <div class="abs" style="left:28px;top:42px;width:200px;font-size:6.8px;color:#666;line-height:1.45">Sed ut perspiciatis unde omnis iste natus error sit volup tatem accus antium dolor emque lauda nt ium, totam rem aperiam, eaque ipsa quae ab illo.</div>
  <div class="abs" style="left:28px;top:81px;font-size:6.5px;color:#888;line-height:12px">
    <div><span style="color:var(--green)">◉</span>&nbsp; Attend our events</div>
    <div><span style="color:var(--green)">◉</span>&nbsp; Download our free guides</div>
    <div><span style="color:var(--green)">◉</span>&nbsp; Ask about a workshop in your city</div>
    <div style="line-height:9px;padding-top:2px"><span style="color:var(--green)">◉</span>&nbsp; Collaborate with a Bright Towns<br>&nbsp;&nbsp;&nbsp;&nbsp; Forum task force</div>
  </div>
  <div class="abs" style="left:26px;top:159px;width:170px;height:35px;background:var(--orange);color:#fff;font-size:5.3px;font-weight:600;padding:6px 10px;line-height:1.5">We are a famous <span style="color:var(--navy-deep);font-weight:700">DIGITAL COMPANY</span> in United States specialized in Web, Mobile Design/ Development, Mobile Apps and Social Media Marketing .</div>
</section>

<!-- 6 Market size -->
<section class="slide" style="left:802px;top:233px">
  <div class="photo" role="img" aria-label="Soft faded office background" style="left:0;top:0;width:391px;height:170px;background:linear-gradient(180deg,#fff,#f1f3f6)"></div>
  <div class="title">MARKET <b>SIZE</b></div>
  <div class="abs" style="left:28px;top:30px;width:14px;height:2px;background:var(--orange)"></div>
  <div class="brand">Bright Towns Forum</div><div class="pageno">6</div>
  <div class="abs" style="left:15px;top:52px;width:376px;display:flex;text-align:center">
    <div style="flex:1;border-right:1px solid var(--line);height:100px"><svg width="14" height="12"><path d="M1 11h12M3 10V6M6 10V3M9 10V5M12 10V1" stroke="#999"/></svg><div style="font-size:12px;font-weight:600;color:var(--navy);margin-top:7px">$757 <span style="font-weight:400">B</span></div><div style="font-size:7px;color:var(--orange)">BY 2020</div><div class="small" style="margin-top:3px">19% CAGR (compound<br>annual growth rate)<br><br>Metric &amp; Measure</div></div>
    <div style="flex:1;border-right:1px solid var(--line);height:100px"><svg width="14" height="12"><circle cx="7" cy="4" r="3" fill="none" stroke="#999"/><path d="M2 12c0-4 10-4 10 0" fill="none" stroke="#999"/></svg><div style="font-size:12px;font-weight:600;color:var(--navy);margin-top:7px">$1.38 <span style="font-weight:400">T</span></div><div style="font-size:7px;color:var(--orange)">BY 2020</div><div class="small" style="margin-top:3px">20% CAGR overall,<br>38% CAGR Asia-Pacific<br><br>Northgate Insights</div></div>
    <div style="flex:1;border-right:1px solid var(--line);height:100px"><svg width="14" height="12"><path d="M7 11L2 6a3 3 0 0 1 5-4 3 3 0 0 1 5 4z" fill="none" stroke="#999"/></svg><div style="font-size:12px;font-weight:600;color:var(--navy);margin-top:7px">$1.45 <span style="font-weight:400">T</span></div><div style="font-size:7px;color:var(--orange)">BY 2020</div><div class="small" style="margin-top:3px">Trendora</div></div>
    <div style="flex:1;height:100px"><svg width="14" height="12"><path d="M3 7l5-5 4 4-5 5z" fill="none" stroke="#999"/></svg><div style="font-size:12px;font-weight:600;color:var(--navy);margin-top:7px">$41 <span style="font-weight:400">T</span></div><div style="font-size:7px;color:var(--orange)">BY 2020</div><div class="small" style="margin-top:3px">Cumulative spend<br>over 20 years<br>Civic Systems<br>Institute</div></div>
  </div>
  <div class="abs" style="left:0;top:170px;width:391px;height:50px;background:var(--navy)"></div>
  <div class="abs" style="left:20px;top:178px;font-size:8.3px;font-weight:700;color:#fff">PRAESENT MALESUADA TEMPUS</div>
  <div class="abs" style="left:20px;top:193px;width:190px;font-size:5.7px;color:#c8d3e6;line-height:1.6">Praesent malesuada tempus sapien in consectetur. Nullam eu lobortis nisl. Etiam placerat quis dui non varius.</div>
  <div class="pill" style="left:249px;top:186px;width:116px;height:13px;background:#fff;color:var(--navy);font-size:5px;justify-content:flex-start"><span style="width:20px;height:13px;border-radius:7px;background:var(--orange)"></span><span style="margin-left:20px">www.yoursite.com</span></div>
</section>

<!-- 7 World map -->
<section class="slide" style="left:6px;top:459px">
  <div class="stripe"></div>
  <div class="title">WORLD <b>MAP</b></div>
  <div class="brand">Bright Towns Forum</div><div class="pageno">7</div>
  <div class="photo" role="img" aria-label="World map with Europe and Asia in blue, Africa in orange, the Americas in navy and other land in grey" style="left:122px;top:62px;width:195px;height:128px;background:linear-gradient(120deg,#dbe3ef 0%,#e6e8eb 50%,#d9dce0 100%)"></div>
  <div class="abs" style="left:26px;top:48px;width:90px;text-align:right"><div class="region-name">15% <b style="color:var(--blue)">Europe</b></div><div class="small" style="font-size:5.8px">The quick, brown fox<br>jumps over a lazy<br>dog.</div></div>
  <div class="abs" style="left:315px;top:48px"><div class="region-name">15% <b>Africa</b></div><div class="small" style="font-size:5.8px">The quick, brown fox<br>jumps over a lazy<br>dog.</div></div>
  <div class="abs" style="left:23px;top:139px;width:90px;text-align:right"><div class="region-name">15% <b>America</b></div><div class="small" style="font-size:5.8px">The quick, brown fox<br>jumps over a lazy<br>dog.</div></div>
  <div class="abs" style="left:315px;top:139px"><div class="region-name">15% <b>Asia</b></div><div class="small" style="font-size:5.8px">The quick, brown fox<br>jumps over a lazy<br>dog.</div></div>
</section>

<!-- 8 Multi column table -->
<section class="slide" style="left:404px;top:459px">
  <div class="stripe"></div>
  <div class="title">MULTI COLUMN <b>TABLE</b></div>
  <div class="brand">Bright Towns Forum</div><div class="pageno">8</div>
  <svg class="abs" style="left:36px;top:50px" width="80" height="34" viewBox="0 0 80 34"><circle cx="17" cy="17" r="15" fill="none" stroke="#17335f" stroke-width="1.6"/><path d="M11 11l12 12M23 11l-12 12" stroke="#17335f" stroke-width="2"/><circle cx="63" cy="17" r="15" fill="none" stroke="#17335f" stroke-width="1.6"/><path d="M63 9v16M60 10h6" stroke="#17335f" stroke-width="2"/></svg>
  <div class="abs" style="left:128px;top:50px;font-size:8px;color:var(--orange)">Company budget files 2017</div>
  <div class="abs" style="left:128px;top:63px;width:145px;font-size:6.5px;color:#999;font-style:italic;line-height:1.5;text-align:justify">Lorem ipsum dolor sit amet, ligula suspendisse nulla pretium, rhoncus tempor fermentum.</div>
  <div class="abs" style="left:34px;top:105px;width:240px;font-size:6.5px;color:#777">
    <div style="display:flex;color:var(--orange);font-size:8px;border-bottom:1px solid var(--line);padding-bottom:2px"><span style="width:118px">Nisl rhoncus turpis</span><span style="width:76px">2014</span><span>2015</span></div>
    <div style="display:flex;border-bottom:1px solid var(--line);line-height:12px"><span style="width:118px">Praesent condimentum</span><span style="width:76px">4.456</span><span>4.456</span></div>
    <div style="display:flex;border-bottom:1px solid var(--line);line-height:12px"><span style="width:118px">Praesent condimentum</span><span style="width:76px">5.345</span><span>5.345</span></div>
    <div style="display:flex;border-bottom:1px solid var(--line);line-height:12px"><span style="width:118px">Praesent condimentum</span><span style="width:76px">6.567</span><span>6.567</span></div>
    <div style="display:flex;border-bottom:1px solid var(--line);line-height:12px"><span style="width:118px">Praesent condimentum</span><span style="width:76px">8.789</span><span>8.789</span></div>
    <div style="color:var(--orange);font-size:8px;padding-top:2px;border-bottom:1px solid var(--blue);width:88px">CHANGE 20%</div>
  </div>
  <div class="abs" style="left:276px;top:48px;width:101px;font-size:6px;color:#fff">
    <div style="background:var(--navy);font-size:8.5px;font-weight:600;padding:3px 12px">STATS MANAGER</div>
    <div style="background:var(--blue-soft);padding:4px 19px;border-bottom:1px solid #fff">THIS YEAR<br><b style="font-size:6.8px">17,250</b></div>
    <div style="background:var(--blue-soft);padding:4px 19px;border-bottom:1px solid #fff">THIS MONTH<br><b style="font-size:6.8px">3,000</b></div>
    <div style="background:var(--blue-soft);padding:4px 19px;border-bottom:1px solid #fff">THIS WEEK<br><b style="font-size:6.8px">450</b></div>
    <div style="background:var(--blue-soft);padding:4px 19px">TODAY<br><b style="font-size:6.8px">225</b></div>
  </div>
</section>

<!-- 9 Two pictures -->
<section class="slide" style="left:802px;top:459px">
  <div class="stripe"></div>
  <div class="title">TWO <b>PICTURES</b></div>
  <div class="brand">Bright Towns Forum</div><div class="pageno">9</div>
  <div class="photo" role="img" aria-label="City skyline at sunset" style="left:18px;top:56px;width:129px;height:83px;background:linear-gradient(180deg,#c8a987,#8a8073 50%,#4e5560)"></div>
  <div class="abs" style="left:147px;top:56px;width:115px;height:83px;background:var(--navy);text-align:center;color:#fff">
    <div style="font-size:10px;font-weight:600;margin-top:7px">HEADING TEXT</div>
    <div style="font-size:6.3px;line-height:1.5;margin:3px 14px 0">Lorem ipsum dolor sit amet, consec tetur adip iscing</div>
    <div class="pill" style="left:10px;top:60px;width:82px;height:11px;background:var(--orange);color:#fff;font-size:5px;justify-content:flex-start"><span style="width:18px;height:11px;border-radius:6px;background:var(--navy-deep)"></span><span style="margin-left:26px">Visit Us</span></div>
  </div>
  <div class="photo" role="img" aria-label="Downtown skyline under a cloudy sky" style="left:262px;top:56px;width:129px;height:83px;background:linear-gradient(180deg,#b8c4cf,#7b8894 55%,#4a5560)"></div>
  <div class="abs" style="left:50px;top:164px;width:300px;text-align:center;font-size:6.3px;color:#777;line-height:1.55">Lorem ipsum dolor sit amet, consec tetur adip iscing elit, sed do eiusmod tempor consec tetur adip iscing elit, sed do eiusmod tempor consec tetur adip iscing elit, sed do eiusmod tempor consec elit.</div>
</section>

<!-- 10 Monthly timeline -->
<section class="slide" style="left:6px;top:686px">
  <div class="stripe"></div>
  <div class="title">MONTHLY <b>TIMELINE</b></div>
  <div class="brand">Bright Towns Forum</div><div class="pageno">10</div>
  <svg class="abs" style="left:0;top:0" width="391" height="220" viewBox="0 0 391 220">
    <line x1="40" y1="125" x2="358" y2="125" stroke="#999" stroke-width="1"/>
    <g fill="#555"><circle cx="46" cy="125" r="2.2"/><circle cx="74" cy="125" r="2.2"/><circle cx="103" cy="125" r="2.2"/><circle cx="131" cy="125" r="2.2"/><circle cx="159" cy="125" r="2.2"/><circle cx="188" cy="125" r="2.2"/><circle cx="216" cy="125" r="2.2"/><circle cx="244" cy="125" r="2.2"/><circle cx="272" cy="125" r="2.2"/><circle cx="301" cy="125" r="2.2"/><circle cx="329" cy="125" r="2.2"/><circle cx="356" cy="125" r="2.2"/></g>
    <g stroke="#bbb"><line x1="46" y1="84" x2="46" y2="123"/><line x1="159" y1="86" x2="159" y2="123"/><line x1="329" y1="83" x2="329" y2="123"/><line x1="131" y1="127" x2="131" y2="178"/><line x1="244" y1="127" x2="244" y2="188"/></g>
    <circle cx="41" cy="72" r="9" fill="#3b6cb3"/><circle cx="154" cy="85" r="9" fill="#8bbf3a"/><circle cx="323" cy="73" r="9" fill="#17335f"/><circle cx="125" cy="188" r="9" fill="#f28a1c"/><circle cx="238" cy="198" r="9" fill="#7d5ba6"/>
    <g fill="none" stroke="#fff" stroke-width="1"><circle cx="41" cy="71" r="3"/><path d="M40 75h2"/><circle cx="154" cy="85" r="3.5"/><rect x="319" y="70" width="8" height="6"/><path d="M322 70v-1.5h2V70"/><rect x="121" y="184" width="8" height="8"/><path d="M234 201l6-6 2 2-6 6h-2z"/></g>
    <g font-size="7" fill="#3b6cb3" font-family="Open Sans,sans-serif" text-anchor="middle">
      <text x="74" y="118">February</text><text x="131" y="118">April</text><text x="188" y="118">June</text><text x="244" y="118">August</text><text x="301" y="118">October</text>
      <text x="103" y="138">March</text><text x="159" y="138">May</text><text x="216" y="138">July</text><text x="272" y="138">September</text><text x="329" y="138">November</text>
    </g>
    <text x="46" y="138" text-anchor="middle" font-size="7" font-weight="600" fill="#17335f" font-family="Open Sans,sans-serif">January</text>
    <text x="46" y="147" text-anchor="middle" font-size="7" fill="#333" font-family="Open Sans,sans-serif">2017</text>
    <text x="356" y="108" text-anchor="middle" font-size="7" fill="#333" font-family="Open Sans,sans-serif">2017</text>
    <text x="356" y="118" text-anchor="middle" font-size="7" font-weight="600" fill="#17335f" font-family="Open Sans,sans-serif">December</text>
  </svg>
  <div class="abs note" style="left:56px;top:60px">Lorem Ipsum is<br>simply <b>dummy</b><br><b>text</b></div>
  <div class="abs note" style="left:170px;top:73px">Lorem Ipsum is<br>simply <b>dummy</b><br><b>text</b></div>
  <div class="abs note" style="left:260px;top:56px;text-align:right">Lorem Ipsum is<br>simply <b>dummy</b><br><b>text</b></div>
  <div class="abs note" style="left:141px;top:176px">Lorem Ipsum is<br>simply <b>dummy</b><br><b>text</b></div>
  <div class="abs note" style="left:253px;top:186px">Lorem Ipsum is<br>simply <b>dummy</b><br><b>text</b></div>
</section>

<!-- 11 Linear process -->
<section class="slide" style="left:404px;top:686px">
  <div class="stripe"></div>
  <div class="title">LINEAR <b>PROCESS</b></div>
  <div class="brand">Bright Towns Forum</div><div class="pageno">11</div>
  <svg class="abs" style="left:0;top:0" width="391" height="220" viewBox="0 0 391 220">
    <g stroke="#bbb"><line x1="84" y1="52" x2="84" y2="112"/><line x1="197" y1="52" x2="197" y2="112"/><line x1="310" y1="52" x2="310" y2="112"/><line x1="30" y1="130" x2="30" y2="180"/><line x1="143" y1="130" x2="143" y2="180"/><line x1="257" y1="130" x2="257" y2="180"/></g>
    <polygon points="24,112 83,112 89,120 83,128 24,128" fill="#17335f"/>
    <polygon points="83,112 139,112 145,120 139,128 83,128 89,120" fill="#6f97cf"/>
    <polygon points="139,112 196,112 202,120 196,128 139,128 145,120" fill="#8bbf3a"/>
    <polygon points="196,112 252,112 258,120 252,128 196,128 202,120" fill="#f28a1c"/>
    <polygon points="252,112 309,112 315,120 309,128 252,128 258,120" fill="#ee5b2a"/>
    <polygon points="309,112 370,112 376,120 370,128 309,128 315,120" fill="#7d5ba6"/>
    <g font-size="7.2" fill="#fff" font-family="Open Sans,sans-serif" text-anchor="middle"><text x="56" y="123">EXECUTE</text><text x="115" y="123">REVIEW</text><text x="172" y="123">INDICATE</text><text x="228" y="123">IDENTIFY</text><text x="285" y="123">CHECKING</text><text x="343" y="123">CONFIRM</text></g>
    <g fill="none" stroke="#999" stroke-width=".9"><rect x="86" y="56" width="12" height="12"/><path d="M88 60h8M88 63h8"/><circle cx="207" cy="60" r="5"/><path d="M203 64l-4 4"/><path d="M316 68v-8l4-5v5h6v8z"/><circle cx="37" cy="144" r="5"/><circle cx="37" cy="144" r="2"/><path d="M150 151l9-9 2 2-9 9h-2z"/><path d="M264 140h12v8h-8l-4 3z"/></g>
  </svg>
  <div class="abs" style="left:86px;top:79px;font-size:6.8px;color:#333;line-height:1.4">Vestibulum<br>lobortis libero.</div>
  <div class="abs" style="left:199px;top:79px;font-size:6.8px;color:#333;line-height:1.4">Vestibulum<br>lobortis libero.</div>
  <div class="abs" style="left:312px;top:79px;font-size:6.8px;color:#333;line-height:1.4">Vestibulum<br>lobortis libero.</div>
  <div class="abs" style="left:30px;top:160px;font-size:6.8px;color:#333;line-height:1.4">Vestibulum<br>lobortis libero.</div>
  <div class="abs" style="left:143px;top:160px;font-size:6.8px;color:#333;line-height:1.4">Vestibulum<br>lobortis libero.</div>
  <div class="abs" style="left:257px;top:160px;font-size:6.8px;color:#333;line-height:1.4">Vestibulum<br>lobortis libero.</div>
</section>

<!-- 12 Thank you -->
<section class="slide" style="left:802px;top:686px">
  <div class="photo" role="img" aria-label="Dusky aerial cityscape tinted navy" style="left:0;top:0;width:391px;height:220px;background:linear-gradient(180deg,#3b5478,#2a4066 50%,#1e3050)"></div>
  <div class="stripe"></div>
  <div class="abs" style="left:0;top:53px;width:391px;text-align:center;font-size:20px;font-weight:700;color:#fff">THANK <span class="orange">YOU</span></div>
  <div class="abs" style="left:80px;top:86px;width:240px;text-align:center;font-size:7.6px;color:#d6deea;line-height:1.5">Praesent malesuada tempus sapien in consectetur. Nullam eu lobortis nisl. Etiam placerat quis dui non varius.</div>
  <svg class="abs" style="left:0;top:115px" width="391" height="20" viewBox="0 0 391 20"><circle cx="152" cy="9" r="8" fill="#6f97cf"/><rect x="148" y="6" width="8" height="6" fill="none" stroke="#fff"/><circle cx="205" cy="9" r="8" fill="#f28a1c"/><path d="M202 5c1 3 3 5 6 6" stroke="#fff" stroke-width="1.5" fill="none"/><circle cx="258" cy="9" r="8" fill="#8bbf3a"/><circle cx="258" cy="9" r="4" fill="none" stroke="#fff"/></svg>
  <div class="abs" style="left:131px;top:138px;font-size:6.2px;color:#fff">info@site.com</div>
  <div class="abs" style="left:188px;top:138px;font-size:6.2px;color:#fff">1-234-5678</div>
  <div class="abs" style="left:238px;top:138px;font-size:6.2px;color:#fff">www.site.com</div>
  <div class="pill" style="left:128px;top:160px;width:152px;height:18px;background:#fff;color:var(--navy);font-size:8px;font-weight:600">Bright Towns Forum</div>
</section>

</div>
</body>
</html>
```